website design + images

We need a very appealing website design, layout and images for a sales analytics and sales productivity services company based in San Ramon, California. We need a good design for the home page and a template for all other pages (total 2 designs), and images for all inner pages (center column/banner images, and right hand top corner small images). There are about 18 inner pages.
Updates

Our existing website is www.brightvale.com
Our corporate colours are the ones that are there on the website. The logo is also shown. We will be changing the tagline to "accelerating revenue" or equivalent of that.

Please use the document "website for brightvale - template v2.doc" that I just uploaded for any reference to the content, navigation and wireframes. A few more clarifications are provided mainly for the link "Solutions".

Rajesh Kothuri

Hi,
We just uploaded ver 4 of the website template. There is more elaboration provided around the sublinks / sections for Solutions. Pls review and do get back if you need any clarifications.

Rgds
Rajesh Kothuri

Hi all,
We have so far received a few good designs. The designs are more or less on the right track. I would like to urge all of you to use the content and navigation provided in the document attached to our brief "website for brightvale - template v4.doc".  Please DO NOT use the content in our existing website www.brightvale.com . That is very old. We mentioned it only for reference to colour theme and broad details.

We have totally 13 sections in Solutions pages. They may be designed as a tree of links - first level sublinks - second level sublinks or links - first level sublinks and the remaining as sections within the first level sublinks pages. The page design would remain the same for all inner pages except careers. But after finalizing the design for the inner page, we will need images for the different inner pages.

Rgds
Rajesh Kothuri

Hi,
Thank you all for participation and very good designs. We are quite happy with what we have seen. We have now shortlisted about 4 vendors and sending invididual feedback to them for further improvement. We will be finalizing by Monday or Tuesday.  To the vendors who do not get feedback from us, thank you very much for participation. We may still do business in future for some of our other needs. 
The following are the process steps / expectations going forward, 
1. Feedback to the shortlisted designers and inviting improvements.
2. Review of the improved designs and further shortlist & feedback or direct finalization.
3. The design should be in 1024*768
2. Number of page designs = 2 (home page, inner page).
4. Home page design: instead of delivery model and customers, show one link "Why Us".
4. Solutions page design:  We will be needing an image in center column of solutions page that in a nutshell gives all the different types of solutions we provide. The entire set of solutions is in our attached document website for brightvale - template v4 and I am just uploading v5 with more description on sublinks.
5. After selection, we will be needing images for all the solution pages (total 12 pages under solutions + one solutions page), 1 image for Why Us?, 1 for Careers, and 3 for company (about us/ team, core values, ...) = total 18

Rgds
Rajesh Kothuri

Target Market(s)

We are a sales analytics and sales productivity services company. We help B2B companies with: sales planning; sales operations and sales measurement. The characteristics of our customers are:
- B2B medium enterprises (USD 100M- USD 2B in revenue) in the US
- Primary target verticals are: high-tech, engineering and professional services firms
- Our primary target customers titles are VP of Sales or VP of marketing; we could be selling to the CEO at companies with revenues below $200M

Industry/Entity Type

Consulting

Requirements
Must have
• - Clean, uncluttered design
• - Easy navigation; minimum clicks
Nice to have
• We have already built a content management system and wireframes for this site. To the extent possible, it would be great to leverage the wireframe structure we built, provided you don’t have to compromise on the look and feel and navigation of the site. Below is what we currently have as banner sizes and resolutions are:
• Home page banner size: 950 * 250’
• All pages – center top - image size: 558 * 160
• All pages – right hand top image – 175*135’

```html
<!DOCTYPE html>
<html lang="en">
<head>
<meta charset="utf-8">
<title>Brightvale – Solutions</title>
<link rel="stylesheet" href="https://fonts.googleapis.com/css2?family=Arimo:wght@400;700&family=PT+Sans:wght@400;700&display=swap">
<style>
  :root {
    --blue-bar: #0b6bb5;
    --blue-bar-dark: #075a9c;
    --blue-link: #0a64b6;
    --blue-nav: #1566ae;
    --green: #4f9a3c;
    --green-dark: #3d8a2d;
    --green-caption: #5d9f4c;
    --text: #222222;
    --grey-line: #d9d9d9;
    --footer-text: #ffffff;
  }
  * { box-sizing: border-box; margin: 0; padding: 0; }
  html, body { width: 1200px; height: 798px; overflow: hidden; }
  body {
    font-family: "Arimo", Arial, sans-serif;
    color: var(--text);
    background: linear-gradient(#ffffff 0, #f4f4f4 120px, #ffffff 200px, #f0f0f0 380px, #a9a9a9 700px, #9a9a9a 798px);
  }
  .canvas { position: relative; width: 1200px; height: 798px; }

  /* Utility bar */
  .utility-bar {
    position: absolute; left: 0; top: 0; width: 1200px; height: 42px;
    background: linear-gradient(var(--blue-bar), var(--blue-bar-dark));
  }
  .utility-link {
    position: absolute; top: 0; height: 42px; display: flex; align-items: center; gap: 7px;
    color: #fff; font-family: "PT Sans", sans-serif; font-size: 14.5px; text-transform: uppercase; letter-spacing: -0.2px;
  }
  .utility-link.signin {
    left: 54px; width: 160px; height: 51px; padding-left: 8px; align-items: flex-start; padding-top: 11px;
    background: linear-gradient(#73b660, #4f9a3c); border-radius: 0 0 5px 5px;
    box-shadow: 0 1px 2px rgba(0,0,0,.3);
  }
  .utility-link .icon {
    width: 20px; height: 20px; border-radius: 50%; background: #fff; display: inline-flex;
    align-items: center; justify-content: center;
  }

  /* Main card */
  .card {
    position: absolute; left: 48px; top: 150px; width: 1090px; height: 600px;
    background: #fff; border-radius: 0 0 12px 12px;
  }

  /* Brand */
  .brand { position: absolute; left: 62px; top: 100px; display: flex; align-items: center; gap: 10px;
    font-family: "PT Sans", sans-serif; font-weight: 700; font-size: 32px; color: #1a5fa8; }
  .brand-dot { width: 16px; height: 16px; border-radius: 50%; background: #1a5fa8; }

  /* Main nav */
  .main-nav { position: absolute; right: 77px; top: 116px; display: flex; align-items: center; height: 23px; font-weight: 700; font-size: 14px; color: var(--blue-nav); }
  .main-nav .sep { margin: 0 8px; color: var(--green); font-weight: 400; }
  .main-nav .active { background: linear-gradient(#5dae49, #3f8e2f); color: #fff; padding: 3px 11px; border-radius: 12px; margin: 0 8px; border: 1px solid #2f7a22; }

  /* Side menu */
  .side-menu { position: absolute; left: 57px; top: 185px; width: 215px; }
  .side-menu .section {
    height: 38px; display: flex; align-items: center; gap: 8px; padding-left: 8px;
    font-family: "PT Sans", sans-serif; font-weight: 700; font-size: 14.5px; color: var(--green);
    background: linear-gradient(#ffffff, #e4e4e4); border: 1px solid #d4d4d4; border-radius: 6px 6px 0 0;
  }
  .side-menu .section + .section { margin-top: 7px; }
  .side-menu .toggle { width: 15px; height: 15px; background: var(--green-dark); border: 1px solid #2d6e20; display: inline-flex; align-items: center; justify-content: center; }
  .side-menu .sub { list-style: none; padding: 14px 15px 8px 14px; background: linear-gradient(#f3f3f3, #fff 20px); margin-bottom: 7px; }
  .side-menu .sub li { font-size: 12px; height: 25px; line-height: 25px; border-bottom: 1px dotted #aaa; padding-left: 12px; position: relative; }
  .side-menu .sub li::before { content: "›"; position: absolute; left: 0; top: -1px; font-weight: 700; }
  .side-menu .sub li.current { font-weight: 700; }
  .side-rule { position: absolute; left: 271px; top: 410px; width: 1px; height: 290px; background: var(--grey-line); }

  /* Banner */
  .hero { position: absolute; left: 284px; top: 185px; width: 626px; height: 181px; background: radial-gradient(ellipse at 60% 20%, #7fe6f6, #1cb3d6 45%, #0a6a99 100%); }
  .hero-copy { position: absolute; left: 13px; top: 95px; color: #fff; font-family: "PT Sans", sans-serif; }
  .hero-copy h2 { font-size: 25px; font-weight: 700; letter-spacing: -0.3px; }
  .hero-copy p { font-size: 15.5px; font-weight: 700; line-height: 19px; }

  /* Right column */
  .aside { position: absolute; left: 926px; top: 185px; width: 197px; }
  .aside-photo { height: 152px; background: linear-gradient(135deg, #4c6a86, #c9d4de 55%, #8a97a3); }
  .aside-caption { height: 29px; background: var(--green-caption); color: #fff; font-family: "PT Sans", sans-serif; font-weight: 700; font-size: 14px; line-height: 29px; padding-left: 8px; }
  .aside-text { padding: 13px 4px 0 12px; font-size: 13.4px; line-height: 19px; text-align: justify; hyphens: manual; }
  .aside-text p + p { margin-top: 19px; }
  .aside-rule { position: absolute; left: 926px; top: 366px; width: 1px; height: 350px; background: var(--grey-line); }

  /* Solutions */
  .page-title { position: absolute; left: 286px; top: 374px; font-family: "PT Sans", sans-serif; font-weight: 700; font-size: 27px; color: var(--green); }
  .solutions { position: absolute; left: 286px; top: 413px; width: 624px; height: 285px; border: 1px solid #e2e2e2; border-bottom: none; border-radius: 9px 9px 0 0; background: linear-gradient(#f6f6f6, #fff 40px); display: flex; padding: 19px 0 0 15px; }
  .solution { width: 211px; padding-right: 20px; }
  .solution + .solution + .solution { width: 213px; }
  .solution h3 { font-family: "PT Sans", sans-serif; font-weight: 700; font-size: 14.5px; line-height: 16px; color: var(--green); }
  .solution p { font-size: 13.4px; line-height: 16.5px; margin-top: 5px; max-width: 168px; }
  .solution ul { list-style: none; margin-top: 8px; }
  .solution li { font-size: 13.4px; line-height: 16.2px; color: var(--blue-link); padding-left: 12px; position: relative; }
  .solution li::before { content: "›"; position: absolute; left: 0; color: var(--green); font-weight: 700; }

  /* Footer */
  .footer { position: absolute; top: 766px; left: 58px; width: 1065px; display: flex; justify-content: space-between; color: var(--footer-text); font-size: 13.4px; }
</style>
</head>
<body>
<div class="canvas">
  <nav class="utility-bar">
    <span class="utility-link signin"><span class="icon"><svg width="12" height="12" viewBox="0 0 12 12"><path d="M1 6h7M5 3l3 3-3 3M9 1h2v10H9" stroke="#4f9a3c" stroke-width="1.6" fill="none"/></svg></span>Sign in / Register</span>
    <span class="utility-link" style="left:227px"><span class="icon"><svg width="12" height="12" viewBox="0 0 12 12"><rect x="4" y="1" width="4" height="3" fill="#0b6bb5"/><rect x="0.5" y="8" width="4" height="3" fill="#0b6bb5"/><rect x="7.5" y="8" width="4" height="3" fill="#0b6bb5"/><path d="M6 4v2M2.5 8V6h7v2" stroke="#0b6bb5" fill="none"/></svg></span>Contact us</span>
    <span class="utility-link" style="left:355px"><span class="icon"><svg width="12" height="12" viewBox="0 0 12 12"><rect x="1" y="2.5" width="10" height="7" fill="none" stroke="#0b6bb5" stroke-width="1.2"/><path d="M1 2.5l5 4 5-4" stroke="#0b6bb5" fill="none"/></svg></span>Sitemap</span>
  </nav>

  <div class="card"></div>

  <div class="brand"><span class="brand-dot"></span>Brightvale</div>

  <nav class="main-nav">
    <span>Home</span><span class="active">Solutions</span><span>Why Us</span><span class="sep">|</span><span>Company</span><span class="sep">|</span><span>Careers</span>
  </nav>

  <aside class="side-menu">
    <div class="section"><span class="toggle"><svg width="9" height="7" viewBox="0 0 9 7"><path d="M0 0h9L4.5 7z" fill="#fff"/></svg></span>Sales Planning Analytics</div>
    <ul class="sub">
      <li>Customer Targeting</li>
      <li>Territory Planning</li>
      <li class="current">Campaign Planning</li>
    </ul>
    <div class="section"><span class="toggle"><svg width="7" height="9" viewBox="0 0 7 9"><path d="M0 0l7 4.5L0 9z" fill="#fff"/></svg></span>Sales Productivity Centers</div>
    <div class="section"><span class="toggle"><svg width="7" height="9" viewBox="0 0 7 9"><path d="M0 0l7 4.5L0 9z" fill="#fff"/></svg></span>Sales Measurement Analytics</div>
  </aside>
  <div class="side-rule"></div>

  <div class="hero" role="img" aria-label="Silhouettes of business people standing before a glowing world map">
    <div class="hero-copy">
      <h2>Do more with less.</h2>
      <p>No upfront software, hardware,<br>people or training costs for you. Pay as you go.</p>
    </div>
  </div>

  <aside class="aside">
    <div class="aside-photo" role="img" aria-label="Hands reviewing sales reports and charts on a desk"></div>
    <div class="aside-caption">Sales Operations Support</div>
    <div class="aside-text">
      <p>Vestibulum lectus arcu, iaculis non iaculis ultrices, ultricies sit amet nisi. Nullam dictum nunc et metus dapibus scelerisque. Etiam quis sapien in purus consequat ornare.</p>
      <p>Praesent vitae ipsum lorem. Nullam ac orci mi, sed pellen&shy;tesque dolor. Nullam dictum nunc et metus dapibus scelerisque. Etiam quis sapien in purus consequat ornare. Praesent vitae ipsum lorem. Nullam ac orci mi, sed pellen&shy;tesque dolor.</p>
    </div>
  </aside>
  <div class="aside-rule"></div>

  <h1 class="page-title">Solutions</h1>
  <section class="solutions">
    <div class="solution">
      <h3>Sales Planning<br>Analytics</h3>
      <p>We help target the right customers, allocate resources effectively and increase return on sales &amp; marketing $.</p>
      <ul><li>Customer Targeting</li><li>Territory Planning</li><li>Campaign Planning</li></ul>
    </div>
    <div class="solution">
      <h3>Sales Operations<br>Support</h3>
      <p>This is all about saving time for sales reps and improv&shy;ing their productivity.</p>
      <ul><li>Quoting center</li><li>Proposal center</li><li>CRM center</li><li>Partner center</li><li>Reference center</li><li>Deal center</li></ul>
    </div>
    <div class="solution">
      <h3>Sales Measurement<br>Analytics</h3>
      <p>This is all about improving sales efficiency by providing actionable insights.</p>
      <ul><li>Business Reporting</li><li>Metrics &amp; Benchmarking</li><li>Pipeline health check</li><li>Sales rep scorecards</li><li>What-if analyses</li><li>Data services.</li></ul>
    </div>
  </section>

  <footer class="footer">
    <span>Contact Us | Sitemap &nbsp;|&nbsp; Disclaimer</span>
    <span>© 2010. Brightvale, Inc. All Rights Reserved</span>
  </footer>
</div>
</body>
</html>
```